Probate (Legal) Wordpress Design with Coding for Online Company

I need a Wordpress design with coding, pictures, content to be provided by me, fully responsive, and development. This is for a 6-7 page design.

Pages Needed: Home/About/Probate/Process/FAQ/Contact Us/Blog.

The home page should be organized as followed:
-Steps in Probate: Gather; Implement; Close (each step will come with content)
-Flat-Fee Price & Savings: Content will go here with a button to contact us (phone number) or just the phone number.
-You Have Questions, We Have Answers: five questions with content. Only one question answer to show at a time when clicked on the question from the list.
-Get to Know Us: a brief description with content about what we do and who we are.

Main image slogan: Helping Californians deal with loss with DIGNITY & UNDERSTATING (you may use a better slogan if you wish).

The Contact page should not have a map since we are an online company. We service the entire state of California in every county and city.

The About page should be simple, direct, and easy on the eye. It should have a brief description of who we are and it should have no more than 6 reasons why the client should hire us.

About our online California company. We are not attorneys but legal document assistants who prepare legal documents for probate estate when someone dies with or without a will and assets need to be distributed. We have a flat-fee for Formal Probate of $999 and $699 for Informal Probate. We are an online company and offer our services to the entire state of California in every county. We do everything over the phone and email. The turn around time for us to prepare the initial legal paperwork for the client is within 3-5 business days. We can prepare, file, serve and manage a probate matter from petition to closing. We are not attorneys so our prices are very affordable compare to the attorney.

The company name for the website will be www.velmarhollow.com, The Velmar Hollow Group.

I do not have a logo yet. The colors of the website should be easy on the eye and calming. THE SITE SHOULD BE SIMPLE AND STRAIGHT TO THE POINT. EASY TO NAVIGATE.

The company phone number should be very visible and should stand out to the client. It should also be clickable and ready to dial for smartphone users.

I do not want a contact form on the homepage. THE MAIN THING IS FOR THE POTENTIAL CLIENT TO CALL OUR OFFICE TO SIGN UP.

I do like some images of family or people since we are dealing with people who just lost a loved one. Not all the images have to be of people.

The site should not look like we practice law or that people can mistake us for attorneys.

Target Market(s)

People who just lost a loved one who had property, assets, in California but died with or without a will or trust. This is for people looking to hire non-attorneys.

Coding

Coded - Design and coding required

Font styles to use
Serif

Colors

Designer to choose colors to be used in the design.

Requirements
Must have
• Refer to Project Description.
Nice to have
• The sample images provided is what I am attracted to for the homepage image.
Should not have

```html
<!DOCTYPE html>
<html lang="en">
<head>
<meta charset="utf-8">
<title>The Velmar Hollow Group</title>
<link href="https://fonts.googleapis.com/css2?family=Lato:wght@400;700;900&display=swap" rel="stylesheet">
<style>
:root{
  --blue:#1f7fd0;
  --blue-dark:#0d5ea8;
  --navy:#15508f;
  --ink:#333a44;
  --muted:#7b818a;
  --line:#d9dde2;
  --footer-top:#0a6fc4;
  --footer-bottom:#0c63b4;
  --footer-bar:#1479d3;
  --white:#ffffff;
}
*{box-sizing:border-box;margin:0;padding:0}
html,body{width:1200px;height:2946px;overflow:hidden}
body{position:relative;font-family:"Lato",Arial,sans-serif;color:var(--ink);background:var(--white)}

/* header */
.site-header{position:absolute;left:0;top:0;width:1200px;height:98px;background:#f6f6f6;display:flex;align-items:center;padding:0 118px}
.brand{font-size:23px;font-weight:700;color:var(--blue-dark);white-space:nowrap}
.main-nav{display:flex;gap:22px;margin-left:34px;font-size:15px;font-weight:700;color:#555b63;white-space:nowrap}
.main-nav .active{color:var(--blue)}
.header-phone{margin-left:auto;display:flex;align-items:center;gap:8px;font-size:18px;font-weight:700;color:var(--navy);white-space:nowrap}

/* hero */
.hero{position:absolute;left:0;top:98px;width:1200px;height:590px;overflow:hidden}
.hero-photo{position:absolute;inset:0;background:linear-gradient(180deg,#c7ccd0 0%,#dcdedf 28%,#d8cabc 55%,#cbb7a3 100%)}
.hero-copy{position:absolute;left:118px;top:140px}
.hero-lead{font-size:33px;line-height:42px;color:var(--blue);padding-left:6px}
.hero-rule{width:480px;height:2px;background:var(--blue);margin:12px 0 8px}
.hero-title{font-size:34px;font-weight:900;color:var(--navy);letter-spacing:.5px;padding-left:4px}
.hero-dots{position:absolute;left:556px;top:460px;display:flex;gap:10px}
.hero-dots span{width:14px;height:14px;border-radius:50%;background:var(--white)}
.hero-dots span:first-child{background:transparent;border:2px solid var(--white)}
.hero-curve{position:absolute;left:0;bottom:0}

/* steps */
.section-title{position:absolute;left:0;width:1200px;text-align:center;font-size:29px;font-weight:700}
.steps-title{top:650px;color:#2b2f35}
.step{position:absolute;top:718px;width:300px;height:300px;border-radius:50%;background:var(--white);box-shadow:0 2px 14px rgba(0,0,0,.13);text-align:center}
.step svg{position:absolute;left:115px;top:36px}
.step h3{position:absolute;top:142px;width:100%;font-size:26px;color:var(--navy);font-weight:700}
.step h3::after{content:"";display:block;width:40px;height:3px;background:var(--blue);margin:9px auto 0}
.step p{position:absolute;top:196px;width:100%;font-size:15px;line-height:25px;color:var(--muted)}
.step-connectors{position:absolute;left:0;top:700px}

/* flat fee */
.fee{position:absolute;left:0;top:1063px;width:1200px;height:473px}
.fee-panel{position:absolute;left:0;top:0;width:571px;height:473px;background:linear-gradient(135deg,#2a94e4 0%,#1d83d6 100%);color:var(--white);padding:112px 0 0 122px}
.fee-panel h2{font-size:30px;font-weight:700;margin-bottom:20px}
.fee-panel p{font-size:14px;line-height:24px;width:410px;margin-bottom:20px}
.btn-outline{display:inline-block;width:167px;height:42px;border:2px solid var(--white);border-radius:3px;text-align:center;line-height:38px;font-size:17px;font-weight:700;color:var(--white)}
.fee-photo{position:absolute;left:571px;top:0;width:629px;height:473px;background:radial-gradient(circle at 12% 42%,#fff6c8 0%,#f7b941 12%,#d97c2a 35%,#6d3a1d 70%,#2a1810 100%)}

/* faq */
.faq-title{top:1585px;color:var(--blue-dark);font-size:32px}
.faq-list{position:absolute;left:122px;top:1672px;width:306px;list-style:none}
.faq-list li{font-size:14px;line-height:36px;border-bottom:1px solid var(--line);color:#333}
.faq-list li.active{color:var(--blue-dark)}
.faq-list li:last-child{border-bottom:none}
.faq-answer{position:absolute;left:463px;top:1668px;width:380px}
.faq-answer h3{font-size:22px;font-weight:400;color:#222;margin-bottom:14px}
.faq-answer p{font-size:13.5px;line-height:25px;color:var(--muted);margin-bottom:12px}
.faq-frame{position:absolute;left:860px;top:1709px;width:195px;height:192px;background:var(--blue)}
.faq-frame-inner{position:absolute;left:875px;top:1669px;width:212px;height:217px;background:var(--white)}
.faq-photo{position:absolute;left:890px;top:1669px;width:194px;height:193px;background:linear-gradient(120deg,#4a3a34 0%,#8c7566 35%,#cfc5bd 70%,#e3e2df 100%)}

/* about */
.about{position:absolute;left:0;top:1984px;width:1200px;height:534px;background:linear-gradient(90deg,#e8e8e8,#f0f0f0 60%,#ececec)}
.about-photo{position:absolute;left:0;top:0;width:650px;height:534px;background:linear-gradient(90deg,#9b9a99 0%,#cfcfcf 45%,#e6e6e6 80%,rgba(236,236,236,0) 100%)}
.about-title{top:2025px;color:#222;font-size:32px;font-weight:400}
.about-block{position:absolute;left:599px;width:500px}
.about-block h3{font-size:23px;font-weight:400;color:var(--blue);margin-bottom:10px}
.about-block p{font-size:13.5px;line-height:24px;color:#6f747b;margin-bottom:12px}

/* footer */
.site-footer{position:absolute;left:0;top:2518px;width:1200px;height:359px;background:linear-gradient(180deg,var(--footer-top),var(--footer-bottom))}
.footer-col{position:absolute;top:84px;color:var(--white)}
.footer-col h4{font-size:17px;font-weight:700;letter-spacing:.4px;margin-bottom:16px}
.footer-col li{list-style:none;font-size:13.5px;line-height:30px;color:#d9e9f7}
.contact-item{display:flex;gap:10px;align-items:flex-start}
.social{display:flex;gap:7px}
.social span{width:44px;height:44px;border:2px solid var(--white);border-radius:50%}
.footer-bar{position:absolute;left:0;top:2877px;width:1200px;height:69px;background:var(--footer-bar);text-align:center;line-height:69px;font-size:13px;color:#b9d8f2}
</style>
</head>
<body>

<header class="site-header">
  <div class="brand">The Velmar Hollow Group</div>
  <nav class="main-nav">
    <span class="active">Home</span><span>About</span><span>Probate</span><span>Process</span><span>FAQ</span><span>Contact Us</span><span>Blog</span>
  </nav>
  <div class="header-phone">
    <svg width="18" height="18" viewBox="0 0 24 24"><path fill="#1f7fd0" d="M6.6 10.8a15.1 15.1 0 0 0 6.6 6.6l2.2-2.2c.3-.3.7-.4 1-.2 1.1.4 2.3.6 3.6.6.6 0 1 .4 1 1V20c0 .6-.4 1-1 1A17 17 0 0 1 3 4c0-.6.4-1 1-1h3.5c.6 0 1 .4 1 1 0 1.3.2 2.5.6 3.6.1.3 0 .7-.2 1z"/></svg>
    (555) 204 7731
  </div>
</header>

<section class="hero">
  <div class="hero-photo" role="img" aria-label="Photo of a woman sitting alone on a sandy beach looking out at the sea"></div>
  <div class="hero-copy">
    <p class="hero-lead">Helping Californians deal<br>with loss with</p>
    <div class="hero-rule"></div>
    <h1 class="hero-title">DIGNITY &amp; UNDERSTATING</h1>
    <div class="hero-rule"></div>
  </div>
  <div class="hero-dots"><span></span><span></span><span></span><span></span></div>
  <svg class="hero-curve" width="1200" height="90" viewBox="0 500 1200 90"><path d="M0 590 Q600 432 1200 590 Z" fill="#fff"/></svg>
</section>

<h2 class="section-title steps-title">Steps in Probate</h2>

<svg class="step-connectors" width="1200" height="300" viewBox="0 700 1200 300">
  <path d="M382 780 Q430 725 478 780" fill="none" stroke="#8a9096" stroke-width="1.5" stroke-dasharray="3 4"/>
  <path d="M714 958 Q762 1010 810 958" fill="none" stroke="#8a9096" stroke-width="1.5" stroke-dasharray="3 4"/>
</svg>

<article class="step" style="left:113px">
  <svg width="70" height="70" viewBox="0 0 70 70" fill="none" stroke="#1f7fd0" stroke-width="2">
    <circle cx="35" cy="40" r="8"/><path d="M20 66c0-9 7-14 15-14s15 5 15 14"/>
    <path d="M35 26V6M35 6l-4 4M35 6l4 4M24 30 12 18M12 18v6M12 18h6M46 30l12-12M58 18v6M58 18h-6M22 40H4M4 40l4-4M4 40l4 4M48 40h18M66 40l-4-4M66 40l-4 4"/>
  </svg>
  <h3>Gather</h3>
  <p>Donec dictum lectus non odio<br>Cras a ante vitae enim</p>
</article>

<article class="step" style="left:445px">
  <svg width="70" height="70" viewBox="0 0 70 70" fill="none" stroke="#1f7fd0" stroke-width="2">
    <circle cx="35" cy="34" r="7"/><circle cx="35" cy="34" r="13" stroke-dasharray="4 3"/>
    <path d="M4 58h14l10 6h22l14-10M46 4h-12l-10 8M4 16h12"/>
    <circle cx="35" cy="34" r="21" stroke-dasharray="2 4"/>
  </svg>
  <h3>Implement</h3>
  <p>Donec dictum lectus non odio<br>Cras a ante vitae enim</p>
</article>

<article class="step" style="left:777px">
  <svg width="70" height="70" viewBox="0 0 70 70" fill="none" stroke="#1f7fd0" stroke-width="2">
    <circle cx="18" cy="18" r="6"/><circle cx="18" cy="18" r="12" stroke-dasharray="5 3"/>
    <path d="M30 18h14c8 0 8 12 0 12H30c-8 0-8 12 0 12h6"/>
    <circle cx="50" cy="50" r="14"/><path d="M43 50l5 5 9-10"/>
  </svg>
  <h3>Close</h3>
  <p>Donec dictum lectus non odio<br>Cras a ante vitae enim</p>
</article>

<section class="fee">
  <div class="fee-panel">
    <h2>Flat-Fee Price &amp; Savings</h2>
    <p>Vivamus porttitor purus nisi eleifend libero a tempus libero lectus feugiat felis Morbi diam mauris viverr</p>
    <p>nonummy nibh ligula pulvinar metus eget consectetuer augue nisi quis lacus Ut ac mi quis lacus mollis aliquam Curabitur iaculis tempus eros Curabitur vel mi sit amet magna</p>
    <span class="btn-outline">Contact Us</span>
  </div>
  <div class="fee-photo" role="img" aria-label="Photo of a person on a swing beside an empty swing at sunset by the sea"></div>
</section>

<h2 class="section-title faq-title">You Have Questions</h2>
<ul class="faq-list">
  <li class="active">Mauris vel lacus vitae felis vestibulum ?</li>
  <li>Volutpat Etiam est nunc venenatis ?</li>
  <li>An tristique eu imperdiet ac nisl Cum sociis ?</li>
  <li>Satoque penatibus et magnis ?</li>
  <li>Dis parturient montes nascetur ridiculus mus ?</li>
</ul>
<div class="faq-answer">
  <h3>Mauris vel lacus vitae felis vestibulum ?</h3>
  <p>Morbi porta libero id ullamcorper nonummy nibh ligula pulvinar metus eget consectetuer augue nisi quis lacus Ut ac mi quis lacus mollis aliquam Curabitur iaculis tempus eros Curabitur vel mi sit amet magna malesuada</p>
  <p>Altrices Ut nisi erat fermentum vel congue id euismod in elit Fusce ultricies orci ac feugiat suscipit leo</p>
</div>
<div class="faq-frame"></div>
<div class="faq-frame-inner"></div>
<div class="faq-photo" role="img" aria-label="Photo of a thoughtful woman by a window"></div>

<section class="about">
  <div class="about-photo" role="img" aria-label="Photo of a sad woman resting her head on her arms on a sofa"></div>
</section>
<h2 class="section-title about-title">Get to Know Us</h2>
<div class="about-block" style="top:2105px">
  <h3>What we do</h3>
  <p>Morbi porta libero id ullamcorper nonummy nibh ligula pulvinar metus eget consectetuer augue nisi quis lacus Ut ac mi quis lacus mollis aliquam Curabitur iaculis tempus eros Curabitur vel mi sit amet magna malesuada Altrices Ut nisi erat fermentum vel congue id euismod in elit Fusce ultricies orci</p>
</div>
<div class="about-block" style="top:2272px">
  <h3>Who we are</h3>
  <p>Morbi porta libero id ullamcorper nonummy nibh ligula pulvinar metus eget consectetuer augue nisi quis lacus Ut ac mi quis lacus mollis aliquam Curabitur iaculis tempus eros Curabitur vel mi sit amet magna</p>
  <p>malesuada Altrices Ut nisi erat fermentum vel congue id euismod in elit Fusce ultricies orciorbi diam mauris viverra in gravida eu mattis i</p>
</div>

<footer class="site-footer">
  <div class="footer-col" style="left:122px">
    <h4>CONTACT US</h4>
    <ul>
      <li class="contact-item"><svg width="14" height="30" viewBox="0 0 14 30"><path fill="#fff" d="M7 8a5 5 0 0 0-5 5c0 4 5 9 5 9s5-5 5-9a5 5 0 0 0-5-5zm0 7a2 2 0 1 1 0-4 2 2 0 0 1 0 4z"/></svg><span>742 Harbor Lane<br>Fresno, California 93721</span></li>
      <li class="contact-item"><svg width="16" height="30" viewBox="0 0 16 30"><path fill="none" stroke="#fff" stroke-width="1.5" d="M4 9c1 5 3 8 8 10l2-2-3-2-1 1c-2-1-3-2-4-4l1-1-2-3z"/></svg><span>(555) 318-4406</span></li>
      <li class="contact-item"><svg width="16" height="30" viewBox="0 0 16 30"><rect x="1" y="10" width="14" height="10" fill="none" stroke="#fff" stroke-width="1.5"/><path d="M1 10l7 6 7-6" fill="none" stroke="#fff" stroke-width="1.5"/></svg><span>hello@velmarhollow.com</span></li>
    </ul>
  </div>
  <div class="footer-col" style="left:371px">
    <h4>COMPANY</h4>
    <ul><li>Home</li><li>About</li><li>Probate</li><li>Process</li></ul>
  </div>
  <div class="footer-col" style="left:564px">
    <h4>RESOURCES</h4>
    <ul><li>FAQ</li><li>Contact Us</li><li>Blog</li></ul>
  </div>
  <div class="footer-col" style="left:758px">
    <h4>FOLLOW US</h4>
    <div class="social"><span></span><span></span><span></span><span></span></div>
  </div>
</footer>
<div class="footer-bar">© 2017 Company Name  All right reserved</div>

</body>
</html>
```